I need the design of at least 200 icons to suit an app for iphones etc..

The icons can be used by anyone in martial arts or interested in martial arts to text amongst one another similar to emoticons. It is just a fun app to have on your phone.
I do not have a business/product or service.

1: all the colored belts for karate, white , orange , yellow, blue, purple, green, brown and black.... all to look tied around the waist.
2. I need a person figure wearing a white karate uniform and then add that person wearing all the different colored belts. So 8 people in all with the above 8 colored belt designs.
3. I need the same person icon design in a black karate uniform ..... same as a (2)
4. I need the same person icon design in a blue karate uniform with all belt colors as in (2)
5. I need icons of all weapons ,samurai sword, nunchakus , bo, sai (three tipped weapon) Kama (handle with blade on end)
6. I would like some icons of karate man holding the different weapons. This character be only in white uniform with black belt.
7. I would like a karate man icon dressed like a ninja in black with cover on face like a ninja.
8. icons of karate man doing kicks in different positions high kick, low kick , middle kick. maybe some jumping kick positions also
9. icons of little ninja man doing kicks in different positions.
10. animated word designs for Bam, Pow, smash, kapow Keeei,kowabunga, Shazam, Knockout, crash, shatter, demolish, destroy, exterminate,wipeout in at least 3 different fonts and colours per word.
11. Icon pics of , a bomb, atom bomb smoke, ninja throwing star.
12. All country flags. Australia Japan korea USA brazil, China , Englan , etc etc

hopefully i can get about 200 at least different icons that will suit Plimvexors for app store.
Updates

I have updated my payment to guaranteed and increased the budget....lets do this

I have updated my project. I am pretty sure that if i have at least 200 icons that will be sufficient. Thank you for your patience. 

I have increased the prize payment for this project to allow for more interest an designs

Target Market(s)

youth, martial arts interested or practicing people....anyone

Industry/Entity Type

Business

Requirements
Must have
• good animation.at least 200 icons need not move. Same size icons as iphone app emoticons
Nice to have
• the ability to add more icons in future
Should not have
• No guns

```html
<!DOCTYPE html>
<html lang="en">
<head>
<meta charset="utf-8">
<title>Martial Arts Sound Words and Shapes</title>
<link rel="stylesheet" href="https://fonts.googleapis.com/css2?family=Comic+Neue:wght@400;700&display=swap">
<style>
  :root {
    --paper: #ffffff;
    --edge: #5a5a5a;
    --sky: #00aeef;
    --lemon: #e5dc00;
    --tangerine: #eb6a3a;
    --leaf: #41cf55;
    --grape: #8b48a6;
    --ink: #111111;
    --word-sky: #1aaee6;
    --word-leaf: #3dc24f;
    --word-grape: #9a52c0;
  }
  html, body {
    margin: 0;
    padding: 0;
    overflow: hidden;
    background: var(--paper);
  }
  .sheet {
    width: 1200px;
    height: 891px;
    display: block;
    background: var(--paper);
  }
  .shape { stroke: var(--edge); stroke-width: 2.5; }
  .fill-sky { fill: var(--sky); }
  .fill-lemon { fill: var(--lemon); }
  .fill-tangerine { fill: var(--tangerine); }
  .fill-leaf { fill: var(--leaf); }
  .fill-grape { fill: var(--grape); }
  .sound-word {
    font-family: "Comic Neue", "Comic Sans MS", cursive;
    font-weight: 700;
    font-size: 54px;
  }
  .word-sky { fill: var(--word-sky); }
  .word-ink { fill: var(--ink); }
  .word-leaf { fill: var(--word-leaf); }
  .word-grape { fill: var(--word-grape); }
</style>
</head>
<body>
<svg class="sheet" viewBox="0 0 1080 802" xmlns="http://www.w3.org/2000/svg" role="img" aria-label="Comic sound word set with speech shapes">
  <g class="shape-set">
    <path class="shape fill-sky speech-bubble" d="M120,57 H263 Q275,57 275,69 V165 Q275,178 290,186 L297,188 Q270,188 238,178 H120 Q107,178 107,165 V69 Q107,57 120,57 Z"/>
    <circle class="shape fill-lemon dot-lemon" cx="396" cy="128" r="75"/>
    <circle class="shape fill-tangerine dot-tangerine" cx="596" cy="128" r="75"/>
    <path class="shape fill-sky wavy-banner" d="M728,78 Q762,92 795,72 Q830,62 872,76 Q905,62 940,76 Q972,64 1000,74 L990,102 L1012,140 Q975,148 950,178 Q918,150 884,158 Q848,166 810,155 Q778,142 745,150 L720,148 L738,112 Z"/>
    <polygon class="shape fill-tangerine burst" points="35,375 62,345 42,285 78,295 75,240 118,268 138,232 183,268 203,238 228,272 283,222 315,278 358,295 322,325 348,355 317,372 308,410 255,405 195,432 148,400 103,415 80,375"/>
    <ellipse class="shape fill-leaf oval" cx="542" cy="330" rx="123" ry="63"/>
    <rect class="shape fill-grape plate" x="737" y="268" width="303" height="97"/>
  </g>
  <g class="word-set" lengthAdjust="spacingAndGlyphs">
    <text class="sound-word word-sky" x="35" y="508" textLength="115" lengthAdjust="spacingAndGlyphs">BAM</text>
    <text class="sound-word word-ink" x="220" y="508" textLength="123" lengthAdjust="spacingAndGlyphs">POW</text>
    <text class="sound-word word-leaf" x="395" y="508" textLength="195" lengthAdjust="spacingAndGlyphs">SMASH</text>
    <text class="sound-word word-ink" x="640" y="508" textLength="190" lengthAdjust="spacingAndGlyphs">KAPOW</text>
    <text class="sound-word word-sky" x="870" y="508" textLength="185" lengthAdjust="spacingAndGlyphs">KEEEII</text>

    <text class="sound-word word-ink" x="25" y="593" textLength="180" lengthAdjust="spacingAndGlyphs">CRASH</text>
    <text class="sound-word word-grape" x="262" y="593" textLength="350" lengthAdjust="spacingAndGlyphs">KOWABUNGA</text>
    <text class="sound-word word-ink" x="676" y="593" textLength="234" lengthAdjust="spacingAndGlyphs">SHAZAM</text>

    <text class="sound-word word-sky" x="38" y="677" textLength="295" lengthAdjust="spacingAndGlyphs">KNOCKOUT</text>
    <text class="sound-word word-ink" x="400" y="677" textLength="248" lengthAdjust="spacingAndGlyphs">SHATTER</text>
    <text class="sound-word word-leaf" x="716" y="677" textLength="289" lengthAdjust="spacingAndGlyphs">DEMOLISH</text>

    <text class="sound-word word-ink" x="37" y="762" textLength="248" lengthAdjust="spacingAndGlyphs">DESTROY</text>
    <text class="sound-word word-grape" x="340" y="762" textLength="395" lengthAdjust="spacingAndGlyphs">ESTERMINATE</text>
    <text class="sound-word word-ink" x="787" y="762" textLength="260" lengthAdjust="spacingAndGlyphs">WIPEOUT</text>
  </g>
</svg>
</body>
</html>
```